Velvet Circle club

We are looking to redesign the user interface of our mobile app “Velvet Circle”, which is the official rewards program for our luxury casino brand, Kestrane Harbour.
Our goal is to give the app a more elegant, premium, and user-friendly design that reflects the exclusivity of our brand and the luxury experience we offer our VIP clientele.
What We Need:
A complete UI design for the app’s main screens, including:
Splash Screen
01 Login / Signup Screen
02 Home Dashboard
Buttons -
Home / my card / my wallet / my booking / my host
My wallet / my offer / lucky game / my taxi / entertainment / online
03 Profile screen
04 My wallet
05 My offer
06Packages
07 My booking
08 My host
09 My card
we attached our privies app all the screen for you reference
Inspiration:
Think of luxury brands like Dunmore-Vale, Corvix Onyx, or high-end lifestyle apps. Clean interfaces, classy animations, and a sense of exclusivity are key.
We’re excited to see fresh, innovative takes that elevate the app to a truly world-class luxury experience for our users.
Thank you!
Casino

```html
<!DOCTYPE html>
<html lang="en">
<head>
<meta charset="utf-8">
<title>Velvet Circle club – App Screens</title>
<link href="https://fonts.googleapis.com/css2?family=Lato:wght@400;700;900&display=swap" rel="stylesheet">
<style>
:root{
  --canvas:#c3c3c3;
  --purple-deep:#3d0a63;
  --purple-mid:#7a1aa8;
  --purple-bright:#9a2cc4;
  --nav-purple:#8c2cc0;
  --gold:#f2c23a;
  --gold-light:#f8dd7c;
  --gold-dark:#b9871d;
  --white:#ffffff;
  --btn-light:#f2f2f2;
  --btn-shade:#cfcfcf;
  --ink:#1c1c1c;
}
*{box-sizing:border-box;margin:0;padding:0}
html,body{width:1200px;height:865px;overflow:hidden;background:var(--canvas);font-family:'Lato',sans-serif}
.screen{position:absolute;top:56px;width:348px;height:754px;overflow:hidden;
  background:radial-gradient(ellipse at 50% 40%,var(--purple-bright) 0%,var(--purple-mid) 45%,var(--purple-deep) 100%)}
.screen--login{left:33px}
.screen--home{left:427px}
.screen--wallet{left:820px}
.abs{position:absolute}
.center{left:0;width:100%;text-align:center}
.frame{position:absolute;inset:0;width:348px;height:754px}
.brand{top:28px}
.brand-dot{width:34px;height:34px;border-radius:50%;background:var(--gold);margin:0 auto 10px}
.brand-name{color:var(--gold);font-weight:900;font-size:30px;line-height:34px;letter-spacing:.5px;text-transform:uppercase}
.heading{color:var(--gold);font-weight:900;text-transform:uppercase}
.copy{color:var(--white);font-size:12.5px;line-height:19px}
.btn{position:absolute;left:86px;width:177px;height:36px;border:2px solid var(--gold);border-radius:5px;padding:3px}
.btn span{display:block;height:100%;border-radius:3px;background:linear-gradient(var(--btn-light),var(--btn-shade));
  color:var(--ink);font-size:16px;line-height:26px;text-align:center}
.divider{left:55px;width:238px;top:384px;height:1px;background:var(--gold)}
.topbar{position:absolute;top:0;left:0;width:100%;height:50px;
  background:linear-gradient(90deg,var(--gold-dark),var(--gold-light) 50%,var(--gold-dark))}
.topbar-title{position:absolute;top:0;width:100%;text-align:center;line-height:50px;font-size:22px;color:var(--ink);font-weight:700}
.hero{left:20px;top:89px;width:307px;height:261px;border:2px solid var(--white);border-radius:24px;
  background:radial-gradient(circle at 50% 50%,#8a6a22 0%,#3a2a10 55%,#0e0a06 100%)}
.tile{position:absolute;width:89px;height:66px;border:1.5px solid #e4d0ff;border-radius:7px;padding:4px}
.tile-face{width:100%;height:100%;border-radius:4px;background:linear-gradient(135deg,var(--gold-light),var(--gold) 50%,var(--gold-dark));
  display:flex;align-items:center;justify-content:center}
.tile-label{position:absolute;width:110px;text-align:center;color:var(--white);font-size:10.5px;font-weight:700}
.navbar{position:absolute;left:0;top:695px;width:100%;height:59px;background:var(--nav-purple)}
.nav-sep{position:absolute;top:14px;width:2px;height:34px;background:#2a0a40}
.nav-ic{position:absolute;top:15px}
.nav-center{position:absolute;left:136px;top:658px;width:76px;height:76px;border-radius:50%;
  background:linear-gradient(135deg,var(--gold-light),var(--gold-dark));border:3px solid #2a0a40;display:flex;align-items:center;justify-content:center}
.coin{position:absolute;left:146px;width:56px;height:56px;border-radius:50%;display:flex;align-items:center;justify-content:center}
.coin--gold{top:292px;background:radial-gradient(circle,#ffcf2a 55%,#f08a12 100%)}
.coin--silver{top:445px;background:radial-gradient(circle,#c9c9c9 55%,#8e8e8e 100%)}
.balance{position:absolute;left:50px;width:249px;height:94px;border:1.5px solid var(--white);border-radius:10px;color:var(--white)}
.balance-title{position:absolute;top:25px;width:100%;text-align:center;font-weight:900;font-size:15px}
.balance-row{position:absolute;left:0;width:100%;display:flex;font-size:15px}
.balance-row span{width:50%;text-align:center}
.balance-row--label{top:47px}
.balance-row--value{top:72px;font-weight:900}
.balance-line{position:absolute;left:20px;right:20px;top:67px;height:1px;background:var(--gold)}
</style>
</head>
<body>

<!-- Login screen -->
<section class="screen screen--login">
  <svg class="frame" viewBox="0 0 348 754" aria-hidden="true">
    <path d="M23,206 L56,167 L123,167 L140,181 L243,181 L259,165 L293,167 L326,203 L326,650 L293,690 L226,690 L210,676 L126,676 L110,690 L56,690 L23,650 Z" fill="none" stroke="#f2c23a" stroke-width="3"/>
  </svg>
  <div class="abs center brand">
    <div class="brand-dot"></div>
    <div class="brand-name">Velvet Circle<br>club</div>
  </div>
  <div class="abs center heading" style="top:216px;font-size:24px">Member Login</div>
  <p class="abs center copy" style="top:262px">Now you can enjoy all the excitement of<br>the casino right at your fingertips.</p>
  <div class="btn" style="top:315px"><span>Sign In</span></div>
  <div class="abs divider"></div>
  <div class="abs center heading" style="top:412px;font-size:15px">New Member Login</div>
  <p class="abs center copy" style="top:441px">If you are a first time user, please go<br>through the sign up process</p>
  <div class="btn" style="top:495px"><span>Sign Up</span></div>
  <div class="abs center" style="top:549px;color:#fff;font-weight:900;font-size:15px">OR</div>
  <p class="abs center copy" style="top:580px">If you are with a temporary ID, sign in here</p>
  <div class="btn" style="top:609px"><span>Temporary Sign In</span></div>
</section>

<!-- Home dashboard -->
<section class="screen screen--home">
  <header class="topbar">
    <svg class="abs" style="left:22px;top:15px" width="32" height="22" viewBox="0 0 32 22"><g stroke="#1c1c1c" stroke-width="3" stroke-linecap="round"><line x1="2" y1="3" x2="26" y2="3"/><line x1="2" y1="11" x2="30" y2="11"/><line x1="2" y1="19" x2="20" y2="19"/></g></svg>
    <svg class="abs" style="left:300px;top:12px" width="30" height="30" viewBox="0 0 30 30"><path d="M5,22 L8,18 L8,12 A7,7 0 0 1 22,12 L22,18 L25,22 Z" fill="#1c1c1c"/><circle cx="15" cy="25" r="3" fill="#1c1c1c"/><circle cx="22" cy="8" r="6" fill="#1c1c1c" stroke="#f8dd7c" stroke-width="1.5"/><text x="22" y="11" font-size="8" fill="#fff" text-anchor="middle" font-family="Lato,sans-serif">1</text></svg>
  </header>
  <div class="abs hero" role="img" aria-label="Casino artwork of golden playing cards and chips scattered on a dark background"></div>

  <div class="tile" style="left:23px;top:397px"><div class="tile-face">
    <svg width="40" height="32" viewBox="0 0 40 32"><rect x="3" y="7" width="32" height="22" rx="4" fill="#2a0a40"/><rect x="24" y="14" width="14" height="9" rx="2" fill="#2a0a40" stroke="#f2c23a" stroke-width="1.5"/><circle cx="29" cy="18.5" r="1.8" fill="#f2c23a"/><path d="M8,7 L26,2 L28,7" fill="#2a0a40"/></svg></div></div>
  <div class="tile-label" style="left:12px;top:481px">MY WALLET</div>

  <div class="tile" style="left:130px;top:397px"><div class="tile-face">
    <svg width="38" height="38" viewBox="0 0 38 38"><polygon points="19,2 24,6 31,5 32,12 37,17 33,23 34,30 27,32 22,37 16,33 9,34 7,27 2,22 6,16 5,9 12,7" fill="#2a0a40"/><g stroke="#f2c23a" stroke-width="2.5"><line x1="13" y1="26" x2="25" y2="12"/></g><circle cx="13" cy="13" r="3" fill="#f2c23a"/><circle cx="25" cy="25" r="3" fill="#f2c23a"/></svg></div></div>
  <div class="tile-label" style="left:119px;top:481px">MY OFFER</div>

  <div class="tile" style="left:236px;top:397px"><div class="tile-face">
    <svg width="36" height="40" viewBox="0 0 36 40"><circle cx="18" cy="16" r="13" fill="none" stroke="#2a0a40" stroke-width="2.5"/><circle cx="18" cy="16" r="7" fill="none" stroke="#2a0a40" stroke-width="2"/><g stroke="#2a0a40" stroke-width="1.5"><line x1="18" y1="3" x2="18" y2="29"/><line x1="5" y1="16" x2="31" y2="16"/><line x1="9" y1="7" x2="27" y2="25"/><line x1="27" y1="7" x2="9" y2="25"/></g><rect x="8" y="32" width="20" height="5" rx="1" fill="#2a0a40"/></svg></div></div>
  <div class="tile-label" style="left:225px;top:481px">Lucky Game</div>

  <div class="tile" style="left:23px;top:513px"><div class="tile-face">
    <svg width="40" height="36" viewBox="0 0 40 36"><rect x="14" y="2" width="12" height="6" rx="1" fill="#2a0a40"/><path d="M8,10 L32,10 L36,20 L36,30 L4,30 L4,20 Z" fill="#2a0a40"/><rect x="11" y="13" width="18" height="6" fill="#f2c23a"/><circle cx="10" cy="24" r="2.5" fill="#f2c23a"/><circle cx="30" cy="24" r="2.5" fill="#f2c23a"/><rect x="6" y="30" width="6" height="5" fill="#2a0a40"/><rect x="28" y="30" width="6" height="5" fill="#2a0a40"/></svg></div></div>
  <div class="tile-label" style="left:12px;top:597px">MY TAXI</div>

  <div class="tile" style="left:130px;top:513px"><div class="tile-face">
    <svg width="40" height="30" viewBox="0 0 40 30"><path d="M3,6 L37,6 L37,12 A4,4 0 0 0 37,20 L37,26 L3,26 L3,20 A4,4 0 0 0 3,12 Z" fill="#2a0a40"/><line x1="26" y1="8" x2="26" y2="24" stroke="#f2c23a" stroke-width="1.5" stroke-dasharray="2 2"/></svg></div></div>
  <div class="tile-label" style="left:119px;top:597px">ENTERTAINMENT</div>

  <div class="tile" style="left:236px;top:513px"><div class="tile-face">
    <svg width="40" height="36" viewBox="0 0 40 36"><rect x="7" y="6" width="26" height="20" rx="2" fill="none" stroke="#2a0a40" stroke-width="2.5"/><path d="M2,29 L38,29 L35,33 L5,33 Z" fill="#2a0a40"/><rect x="14" y="2" width="12" height="16" rx="1.5" fill="#2a0a40"/><rect x="17" y="5" width="6" height="9" fill="#f2c23a"/></svg></div></div>
  <div class="tile-label" style="left:225px;top:597px">ONLINE</div>

  <nav class="navbar">
    <svg class="nav-ic" style="left:24px" width="34" height="32" viewBox="0 0 34 32"><path d="M17,2 L32,16 L28,16 L28,30 L20,30 L20,21 L14,21 L14,30 L6,30 L6,16 L2,16 Z" fill="#f2c23a"/></svg>
    <div class="nav-sep" style="left:72px"></div>
    <svg class="nav-ic" style="left:88px;top:18px" width="36" height="26" viewBox="0 0 36 26"><rect x="1" y="1" width="34" height="24" rx="3" fill="#f2c23a"/><rect x="1" y="7" width="34" height="4" fill="#8c2cc0"/><rect x="5" y="16" width="8" height="3" fill="#8c2cc0"/></svg>
    <svg class="nav-ic" style="left:234px" width="34" height="32" viewBox="0 0 34 32"><rect x="1" y="4" width="32" height="27" rx="2" fill="#f2c23a"/><rect x="1" y="4" width="32" height="6" fill="#d9a627"/><g fill="#8c2cc0"><rect x="5" y="14" width="5" height="4"/><rect x="14" y="14" width="5" height="4"/><rect x="23" y="14" width="5" height="4"/><rect x="5" y="22" width="5" height="4"/><rect x="14" y="22" width="5" height="4"/><rect x="23" y="22" width="5" height="4"/></g></svg>
    <div class="nav-sep" style="left:284px"></div>
    <svg class="nav-ic" style="left:300px" width="28" height="32" viewBox="0 0 28 32"><rect x="3" y="1" width="24" height="30" rx="2" fill="#f2c23a"/><circle cx="16" cy="12" r="5" fill="#8c2cc0"/><path d="M8,25 A8,7 0 0 1 24,25 Z" fill="#8c2cc0"/><g fill="#f2c23a"><rect x="0" y="6" width="5" height="3"/><rect x="0" y="14" width="5" height="3"/><rect x="0" y="22" width="5" height="3"/></g></svg>
  </nav>
  <div class="nav-center">
    <svg width="40" height="32" viewBox="0 0 40 32"><rect x="3" y="9" width="32" height="21" rx="3" fill="none" stroke="#2a0a40" stroke-width="2.5"/><rect x="24" y="15" width="13" height="9" rx="2" fill="none" stroke="#2a0a40" stroke-width="2"/><path d="M8,9 L24,2 L28,9" fill="none" stroke="#2a0a40" stroke-width="2"/></svg>
  </div>
</section>

<!-- Wallet screen -->
<section class="screen screen--wallet">
  <header class="topbar">
    <svg class="abs" style="left:22px;top:14px" width="16" height="24" viewBox="0 0 16 24"><path d="M13,2 L3,12 L13,22" fill="none" stroke="#1c1c1c" stroke-width="2.5"/></svg>
    <div class="topbar-title">MY WALLET</div>
    <svg class="abs" style="left:300px;top:12px" width="30" height="30" viewBox="0 0 30 30"><path d="M5,22 L8,18 L8,12 A7,7 0 0 1 22,12 L22,18 L25,22 Z" fill="#1c1c1c"/><circle cx="15" cy="25" r="3" fill="#1c1c1c"/><circle cx="22" cy="8" r="6" fill="#1c1c1c" stroke="#f8dd7c" stroke-width="1.5"/><text x="22" y="11" font-size="8" fill="#fff" text-anchor="middle" font-family="Lato,sans-serif">1</text></svg>
  </header>
  <svg class="frame" viewBox="0 0 348 754" aria-hidden="true">
    <path d="M22,122 L56,85 L123,85 L137,98 L210,98 L225,85 L293,82 L326,122 L326,590 L293,628 L226,628 L210,640 L126,640 L110,628 L56,628 L22,590 Z" fill="none" stroke="#f2c23a" stroke-width="3"/>
  </svg>
  <div class="btn" style="top:130px"><span>Cash Withdrawal</span></div>
  <div class="abs center heading" style="top:186px;font-size:15px">Need a Fixed Deposit?</div>
  <p class="abs center copy" style="top:207px">We Will Help You Open It Instanly</p>
  <div class="btn" style="top:237px"><span>Open Now</span></div>

  <div class="balance" style="top:331px">
    <div class="balance-title">KESTRANE RUPEES</div>
    <div class="balance-row balance-row--label"><span>Today</span><span>Balance</span></div>
    <div class="balance-line"></div>
    <div class="balance-row balance-row--value"><span>100</span><span>3000</span></div>
  </div>
  <div class="coin coin--gold"><svg width="30" height="30" viewBox="0 0 30 30"><polygon points="15,2 19,11 29,12 21,18 24,28 15,22 6,28 9,18 1,12 11,11" fill="#f08a12"/></svg></div>

  <div class="balance" style="top:484px">
    <div class="balance-title">KESTRANE RUPEES</div>
    <div class="balance-row balance-row--label"><span>Today</span><span>Balance</span></div>
    <div class="balance-line"></div>
    <div class="balance-row balance-row--value"><span>100</span><span>3000</span></div>
  </div>
  <div class="coin coin--silver"><svg width="30" height="30" viewBox="0 0 30 30"><polygon points="15,2 19,11 29,12 21,18 24,28 15,22 6,28 9,18 1,12 11,11" fill="#ffffff"/></svg></div>

  <nav class="navbar">
    <svg class="nav-ic" style="left:24px" width="34" height="32" viewBox="0 0 34 32"><path d="M17,2 L32,16 L28,16 L28,30 L20,30 L20,21 L14,21 L14,30 L6,30 L6,16 L2,16 Z" fill="#f2c23a"/></svg>
    <div class="nav-sep" style="left:72px"></div>
    <svg class="nav-ic" style="left:88px;top:18px" width="36" height="26" viewBox="0 0 36 26"><rect x="1" y="1" width="34" height="24" rx="3" fill="#f2c23a"/><rect x="1" y="7" width="34" height="4" fill="#8c2cc0"/><rect x="5" y="16" width="8" height="3" fill="#8c2cc0"/></svg>
    <svg class="nav-ic" style="left:234px" width="34" height="32" viewBox="0 0 34 32"><rect x="1" y="4" width="32" height="27" rx="2" fill="#f2c23a"/><rect x="1" y="4" width="32" height="6" fill="#d9a627"/><g fill="#8c2cc0"><rect x="5" y="14" width="5" height="4"/><rect x="14" y="14" width="5" height="4"/><rect x="23" y="14" width="5" height="4"/><rect x="5" y="22" width="5" height="4"/><rect x="14" y="22" width="5" height="4"/><rect x="23" y="22" width="5" height="4"/></g></svg>
    <div class="nav-sep" style="left:284px"></div>
    <svg class="nav-ic" style="left:300px" width="28" height="32" viewBox="0 0 28 32"><rect x="3" y="1" width="24" height="30" rx="2" fill="#f2c23a"/><circle cx="16" cy="12" r="5" fill="#8c2cc0"/><path d="M8,25 A8,7 0 0 1 24,25 Z" fill="#8c2cc0"/><g fill="#f2c23a"><rect x="0" y="6" width="5" height="3"/><rect x="0" y="14" width="5" height="3"/><rect x="0" y="22" width="5" height="3"/></g></svg>
  </nav>
  <div class="nav-center">
    <svg width="40" height="32" viewBox="0 0 40 32"><rect x="3" y="9" width="32" height="21" rx="3" fill="none" stroke="#2a0a40" stroke-width="2.5"/><rect x="24" y="15" width="13" height="9" rx="2" fill="none" stroke="#2a0a40" stroke-width="2"/><path d="M8,9 L24,2 L28,9" fill="none" stroke="#2a0a40" stroke-width="2"/></svg>
  </div>
</section>

</body>
</html>
```